Figure for presentation on a hybrid research project

We need a figure that shows a series of 6 technical projects feeding into 3 multidisciplinary hybrid projects.
The concept is a ring of 6 technical projects, which could look like a 6 colour swirl (see
https://en.plorvanex.org/wiki/Vector_graphics for an example of a 4 colour swirl.)
The 3 hybrid projects sit in the centre because they rely on input from many of the surrounding technical projects.
I've drawn a rough version in Powerpoint - see attached file uploaded. Note, in my example I couldn't draw the swirling outer ring and the colour selection is poor. The acronym for the overall Centre using the figure is VexORDA, so we will have a mint leaf and turquoise green in the logo, plus also nerves, since we will be researching neural interconnections.
We ABSOLUTELY NEED the final form of the figure to include vector graphics formats (including a form that can be edited in Photoshop) because we may need to change the title of the technical projects or of the hybrid projects at short notice ourselves.

Target Market(s)

Academic: eminent scientists and engineers

Industry/Entity Type

Technical

Font styles to use
Sans Serif

Colors
04a990

Requirements
Must have
• The projects around the ring with all project titles legible; the final figure will be reduced to no more than 8cm x 8cm in the proposal (probably less).
• Only one colour selected, because we have included that colour in the logo that we are having designed. Otherwise, a colour series around the ring that is pleasant, and another compatible colour series for the inter 3 projects.
• We ABSOLUTELY NEED the final form of the figure to include vector graphics formats (including a form that can be edited in Photoshop) because we may need to change the title of the technical projects or of the hybrid projects at short notice ourselves.
Nice to have
• See the figure we uploaded; that's the essence
• HOWEVER VIP: two of the titles around the outer ring have changed slightly.
• Computational Modelling is now Neuronal Modelling and
• Signal Processing is now Non-Invasive Interfaces (note that I've now changed the titles on the uploaded figure)

```html
<!DOCTYPE html>
<html lang="en">
<head>
<meta charset="utf-8">
<title>Hybrid Research Projects Figure</title>
<link rel="stylesheet" href="https://fonts.googleapis.com/css2?family=Lexend:wght@600;700&display=swap">
<style>
  :root {
    --canvas: #ffffff;
    --gene: #06a186;
    --living: #0b8e72;
    --noninvasive: #077a5e;
    --neuronal: #098a6d;
    --optrode: #078063;
    --electro: #056d53;
    --divider: #ffffff;
    --hub-wiring: #0346c6;
    --hub-action: #02268c;
    --hub-perception: #03245f;
    --label: #ffffff;
  }
  html, body {
    margin: 0;
    padding: 0;
    width: 1200px;
    height: 999px;
    overflow: hidden;
    background: var(--canvas);
  }
  .project-figure {
    display: block;
    width: 1200px;
    height: 999px;
  }
  .petal--gene .petal-fill { fill: var(--gene); }
  .petal--living .petal-fill { fill: var(--living); }
  .petal--noninvasive .petal-fill { fill: var(--noninvasive); }
  .petal--neuronal .petal-fill { fill: var(--neuronal); }
  .petal--optrode .petal-fill { fill: var(--optrode); }
  .petal--electro .petal-fill { fill: var(--electro); }
  .petal-cast { fill: #00241a; opacity: 0.45; }
  .petal-edge { fill: none; stroke: var(--divider); stroke-width: 4; }
  .ring-shade { fill: url(#ringShade); }
  .ring-label {
    font-family: "Lexend", sans-serif;
    font-weight: 600;
    font-size: 26px;
    fill: var(--label);
    letter-spacing: 0.2px;
  }
  .hub-ring { fill: var(--divider); }
  .hub-segment--wiring { fill: var(--hub-wiring); }
  .hub-segment--action { fill: var(--hub-action); }
  .hub-segment--perception { fill: var(--hub-perception); }
  .hub-divider { stroke: var(--divider); stroke-width: 3; fill: none; }
  .hub-label {
    font-family: "Lexend", sans-serif;
    font-weight: 700;
    font-size: 21px;
    fill: var(--label);
    text-anchor: middle;
  }
</style>
</head>
<body>
<svg class="project-figure" viewBox="0 0 1130 941" xmlns="http://www.w3.org/2000/svg" role="img" aria-label="Six technical projects swirling around three hybrid projects">
  <defs>
    <filter id="castBlur" x="-20%" y="-20%" width="140%" height="140%">
      <feGaussianBlur stdDeviation="11"/>
    </filter>
    <filter id="hubShadow" x="-30%" y="-30%" width="160%" height="160%">
      <feDropShadow dx="0" dy="0" stdDeviation="14" flood-color="#00261c" flood-opacity="0.6"/>
    </filter>
    <radialGradient id="ringShade" cx="560" cy="468" r="370" gradientUnits="userSpaceOnUse">
      <stop offset="0.5" stop-color="#003a2c" stop-opacity="0.3"/>
      <stop offset="1" stop-color="#003a2c" stop-opacity="0"/>
    </radialGradient>

    <clipPath id="ringOutline">
      <circle cx="560" cy="373" r="270"/>
      <circle cx="642.3" cy="420.5" r="270"/>
      <circle cx="642.3" cy="515.5" r="270"/>
      <circle cx="560" cy="563" r="270"/>
      <circle cx="477.7" cy="515.5" r="270"/>
      <circle cx="477.7" cy="420.5" r="270"/>
    </clipPath>

    <mask id="under-living" maskUnits="userSpaceOnUse" x="0" y="0" width="1130" height="941">
      <rect width="1130" height="941" fill="#fff"/><circle cx="477.7" cy="420.5" r="270" fill="#000"/>
    </mask>
    <mask id="under-noninvasive" maskUnits="userSpaceOnUse" x="0" y="0" width="1130" height="941">
      <rect width="1130" height="941" fill="#fff"/><circle cx="477.7" cy="515.5" r="270" fill="#000"/>
    </mask>
    <mask id="under-neuronal" maskUnits="userSpaceOnUse" x="0" y="0" width="1130" height="941">
      <rect width="1130" height="941" fill="#fff"/><circle cx="560" cy="563" r="270" fill="#000"/>
    </mask>
    <mask id="under-optrode" maskUnits="userSpaceOnUse" x="0" y="0" width="1130" height="941">
      <rect width="1130" height="941" fill="#fff"/><circle cx="642.3" cy="515.5" r="270" fill="#000"/>
    </mask>
    <mask id="under-electro" maskUnits="userSpaceOnUse" x="0" y="0" width="1130" height="941">
      <rect width="1130" height="941" fill="#fff"/><circle cx="642.3" cy="420.5" r="270" fill="#000"/>
    </mask>
    <mask id="under-gene" maskUnits="userSpaceOnUse" x="0" y="0" width="1130" height="941">
      <rect width="1130" height="941" fill="#fff"/><circle cx="560" cy="373" r="270" fill="#000"/>
    </mask>

    <path id="arc-gene" d="M 432.5 184 A 228 228 0 0 1 744.5 507"/>
    <path id="arc-living" d="M 250.2 436.4 A 228 228 0 0 1 686 327.8"/>
    <path id="arc-noninvasive" d="M 377.7 720.4 A 228 228 0 0 1 501.5 288.8"/>
    <path id="arc-neuronal" d="M 383.1 403.8 A 238 238 0 0 0 671.7 773.1"/>
    <path id="arc-optrode" d="M 415.9 589 A 238 238 0 0 0 880.2 523.8"/>
    <path id="arc-electro" d="M 592.8 653.3 A 238 238 0 0 0 768.4 218.7"/>
  </defs>

  <g class="technical-ring">
    <g class="petal petal--gene" mask="url(#under-living)">
      <circle class="petal-fill" cx="560" cy="373" r="270"/>
      <circle class="petal-cast" cx="477.7" cy="420.5" r="270" filter="url(#castBlur)"/>
    </g>
    <g class="petal petal--living" mask="url(#under-noninvasive)">
      <circle class="petal-fill" cx="477.7" cy="420.5" r="270"/>
      <circle class="petal-cast" cx="477.7" cy="515.5" r="270" filter="url(#castBlur)"/>
    </g>
    <g class="petal petal--noninvasive" mask="url(#under-neuronal)">
      <circle class="petal-fill" cx="477.7" cy="515.5" r="270"/>
      <circle class="petal-cast" cx="560" cy="563" r="270" filter="url(#castBlur)"/>
    </g>
    <g class="petal petal--neuronal" mask="url(#under-optrode)">
      <circle class="petal-fill" cx="560" cy="563" r="270"/>
      <circle class="petal-cast" cx="642.3" cy="515.5" r="270" filter="url(#castBlur)"/>
    </g>
    <g class="petal petal--optrode" mask="url(#under-electro)">
      <circle class="petal-fill" cx="642.3" cy="515.5" r="270"/>
      <circle class="petal-cast" cx="642.3" cy="420.5" r="270" filter="url(#castBlur)"/>
    </g>
    <g class="petal petal--electro" mask="url(#under-gene)">
      <circle class="petal-fill" cx="642.3" cy="420.5" r="270"/>
      <circle class="petal-cast" cx="560" cy="373" r="270" filter="url(#castBlur)"/>
    </g>

    <circle class="ring-shade" cx="560" cy="468" r="380" clip-path="url(#ringOutline)"/>

    <g class="petal-edges">
      <circle class="petal-edge" cx="560" cy="373" r="270" mask="url(#under-living)"/>
      <circle class="petal-edge" cx="477.7" cy="420.5" r="270" mask="url(#under-noninvasive)"/>
      <circle class="petal-edge" cx="477.7" cy="515.5" r="270" mask="url(#under-neuronal)"/>
      <circle class="petal-edge" cx="560" cy="563" r="270" mask="url(#under-optrode)"/>
      <circle class="petal-edge" cx="642.3" cy="515.5" r="270" mask="url(#under-electro)"/>
      <circle class="petal-edge" cx="642.3" cy="420.5" r="270" mask="url(#under-gene)"/>
    </g>
  </g>

  <g class="ring-labels">
    <text class="ring-label"><textPath href="#arc-gene" startOffset="50%" text-anchor="middle">Gene Regulated Interfaces</textPath></text>
    <text class="ring-label"><textPath href="#arc-living" startOffset="50%" text-anchor="middle">Living Electrodes</textPath></text>
    <text class="ring-label"><textPath href="#arc-noninvasive" startOffset="50%" text-anchor="middle">Non-invasive Interfaces</textPath></text>
    <text class="ring-label"><textPath href="#arc-neuronal" startOffset="50%" text-anchor="middle">Neuronal Modeling</textPath></text>
    <text class="ring-label"><textPath href="#arc-optrode" startOffset="50%" text-anchor="middle">Optrode Interfaces</textPath></text>
    <text class="ring-label"><textPath href="#arc-electro" startOffset="50%" text-anchor="middle">Electro-modulated Interfaces</textPath></text>
  </g>

  <g class="hybrid-hub">
    <circle class="hub-ring" cx="560" cy="468" r="184" filter="url(#hubShadow)"/>
    <path class="hub-segment--wiring" d="M 560 468 L 405 381 A 178 178 0 0 1 715 381 Z"/>
    <path class="hub-segment--action" d="M 560 468 L 560 646 A 178 178 0 0 1 405 381 Z"/>
    <path class="hub-segment--perception" d="M 560 468 L 715 381 A 178 178 0 0 1 560 646 Z"/>
    <path class="hub-divider" d="M 560 468 L 405 381 M 560 468 L 715 381 M 560 468 L 560 646"/>
    <text class="hub-label" x="560" y="381">BRAIN WIRING</text>
    <text class="hub-label" x="472" y="519">ACTION</text>
    <text class="hub-label" x="645" y="519">PERCEPTION</text>
  </g>
</svg>
</body>
</html>
```